VENTURE CAPITAL GROUP BUSINESS CARD DESIGN

Venture Capital Group based in SF looking for a bold business card design. No trendy colour explosion, 3D effects etc. Just "simple" optical effects. Works on your brain, keeps your eye focused and sticks to your mind.
Target Market(s)
Technology startups
Industry/Entity Type
Venture Capital
Contact Information for Business Card
DESMOND WHITLAKE
MANAGING PARTNER
187 FENWORTH ST SAN FRANCISCO, CA 94187
415.555.0142 O
415.555.0147 F
415.555.0193 C
desmond@veldtmoorcapital.ventures

```html
<!DOCTYPE html>
<html lang="en">
<head>
<meta charset="utf-8">
<title>Veldtmoor Capital Group — Business Card</title>
<link href="https://fonts.googleapis.com/css2?family=Sorts+Mill+Goudy&family=Libre+Baskerville:wght@700&display=swap" rel="stylesheet">
<style>
  :root {
    --bg: #2a2a2a;
    --card-dark: #1f2421;
    --card-dark-edge: #2b322d;
    --card-light: #f7f7f7;
    --green: #0f7a35;
    --green-bright: #1fa64a;
    --ink: #2b2b2b;
    --divider: #b9b9b9;
  }
  * { margin: 0; padding: 0; box-sizing: border-box; }
  html, body { width: 1200px; height: 873px; overflow: hidden; }
  body {
    background: var(--bg);
    font-family: "Sorts Mill Goudy", Georgia, serif;
    position: relative;
  }
  .card {
    position: absolute;
    width: 560px;
    height: 320px;
    box-shadow: 0 10px 30px rgba(0,0,0,.5);
  }
  .card--front {
    left: 40px; top: 90px;
    background: radial-gradient(ellipse at 50% 40%, var(--card-dark-edge), var(--card-dark) 70%);
    display: flex; flex-direction: column; align-items: center; justify-content: center;
  }
  .brand-dot {
    width: 54px; height: 54px; border-radius: 50%;
    background: var(--green-bright);
    margin-bottom: 22px;
  }
  .brand-name {
    color: var(--green-bright);
    font-size: 40px;
    letter-spacing: 3px;
    text-transform: uppercase;
    text-align: center;
    line-height: 1.1;
  }
  .brand-sub {
    color: var(--green-bright);
    font-size: 15px;
    letter-spacing: 8px;
    text-transform: uppercase;
    margin-top: 6px;
  }
  .card--back {
    left: 600px; top: 463px;
    background: var(--card-light);
  }
  .holder { text-align: center; padding-top: 30px; }
  .holder__name {
    font-family: "Libre Baskerville", Georgia, serif;
    font-weight: 700;
    color: var(--green);
    font-size: 23px;
  }
  .holder__title { color: var(--ink); font-size: 13px; margin-top: 2px; }
  .back-brand {
    text-align: center; margin-top: 20px;
    color: var(--green); font-size: 20px; letter-spacing: 2px;
    text-transform: uppercase;
  }
  .contacts {
    position: absolute; left: 0; right: 0; bottom: 26px;
    display: flex; justify-content: center; align-items: flex-end;
  }
  .contacts__col { list-style: none; display: flex; flex-direction: column; gap: 8px; }
  .contacts__col li { display: flex; align-items: center; gap: 8px; font-size: 15px; color: var(--ink); }
  .contacts__divider {
    width: 2px; height: 104px; margin: 0 16px;
    background: linear-gradient(var(--card-light), var(--divider), var(--card-light));
  }
  .icon { width: 22px; height: 22px; flex: none; }
</style>
</head>
<body>
  <section class="card card--front">
    <div class="brand-dot"></div>
    <div class="brand-name">Veldtmoor</div>
    <div class="brand-sub">Capital Group</div>
  </section>

  <section class="card card--back">
    <header class="holder">
      <div class="holder__name">Desmond Whitlake</div>
      <div class="holder__title">Managing Partner</div>
    </header>
    <div class="back-brand">Veldtmoor Capital Group</div>

    <div class="contacts">
      <ul class="contacts__col">
        <li><svg class="icon" viewBox="0 0 22 22"><circle cx="11" cy="11" r="11" fill="#0f7a35"/><path d="M6 9c0-2 2-3 5-3s5 1 5 3l-2 1-1-2h-4l-1 2z M7 12h8l1 4H6z" fill="#fff"/></svg>415.555.0142</li>
        <li><svg class="icon" viewBox="0 0 22 22"><circle cx="11" cy="11" r="11" fill="#0f7a35"/><path d="M8 6h6v3H8z M6 10h10v5h-2v-2H8v2H6z M8 14h6v3H8z" fill="#fff"/></svg>415.555.0147</li>
        <li><svg class="icon" viewBox="0 0 22 22"><circle cx="11" cy="11" r="11" fill="#0f7a35"/><path d="M7 6l2-1 2 3-1.5 1.5a7 7 0 0 0 3 3L14 11l3 2-1 2c-5 0-9-4-9-9z" fill="#fff"/></svg>415.555.0193</li>
      </ul>
      <div class="contacts__divider"></div>
      <ul class="contacts__col">
        <li><svg class="icon" viewBox="0 0 22 22"><circle cx="11" cy="11" r="11" fill="#0f7a35"/><rect x="5.5" y="7" width="11" height="8" fill="#fff"/><path d="M5.5 7l5.5 4.5L16.5 7" stroke="#0f7a35" fill="none"/></svg>desmond@veldtmoorcapital.ventures</li>
        <li><svg class="icon" viewBox="0 0 22 22"><circle cx="11" cy="11" r="11" fill="#0f7a35"/><path d="M11 17s-4-4.5-4-7.5a4 4 0 0 1 8 0c0 3-4 7.5-4 7.5z" fill="#fff"/><circle cx="11" cy="9.5" r="1.5" fill="#0f7a35"/></svg>187 Fenworth St San Francisco, CA 94187</li>
        <li><svg class="icon" viewBox="0 0 22 22"><circle cx="11" cy="11" r="11" fill="#0f7a35"/><rect x="6" y="9" width="6" height="4" rx="2" fill="none" stroke="#fff" stroke-width="1.6" transform="rotate(-45 9 11)"/><rect x="10" y="9" width="6" height="4" rx="2" fill="none" stroke="#fff" stroke-width="1.6" transform="rotate(-45 13 11)"/></svg>www.veldtmoorcapital.ventures</li>
      </ul>
    </div>
  </section>
</body>
</html>
```